SaaS Early tech startup business card design

Unique design for experience ecommerce platform company. the business cards will be used by executive members. conformance with color code is required.

```html
<!DOCTYPE html>
<html lang="en">
<head>
<meta charset="utf-8">
<title>Quell Business Card</title>
<link rel="stylesheet" href="https://fonts.googleapis.com/css2?family=Open+Sans:wght@400;600;700&display=swap">
<style>
  :root {
    --backdrop: #bdbdbd;
    --card-white: #ffffff;
    --brand-blue: #176691;
    --name-blue: #1d6a99;
    --brand-teal: #1fb89a;
    --ink: #1e1e1e;
  }
  * { margin: 0; padding: 0; box-sizing: border-box; }
  html, body {
    width: 1200px; height: 815px; overflow: hidden;
    background: var(--backdrop);
    font-family: "Open Sans", Arial, sans-serif;
  }
  .stage {
    position: relative; width: 1200px; height: 815px;
    display: flex; align-items: center; justify-content: center; gap: 40px;
  }
  .card {
    position: relative; width: 540px; height: 309px;
    border-bottom: 4px solid var(--brand-teal);
    box-shadow: 0 6px 18px rgba(0,0,0,0.25);
    overflow: hidden;
  }
  .card--front { background: var(--card-white); }
  .card--back {
    background: var(--brand-blue);
    display: flex; align-items: center; justify-content: center;
  }
  .brand-name {
    font-weight: 700; color: var(--brand-teal); letter-spacing: -1px; line-height: 1;
  }
  .card--front .brand-name {
    position: absolute; left: 34px; top: 118px; font-size: 78px; color: var(--name-blue);
  }
  .card--back .brand-name { font-size: 150px; }
  .holder {
    position: absolute; left: 300px; top: 66px;
  }
  .holder__name {
    font-size: 27px; font-weight: 700; color: var(--name-blue); line-height: 1.1;
  }
  .holder__title { font-size: 13px; color: var(--ink); }
  .divider {
    position: absolute; left: 290px; right: 0; top: 124px;
    height: 2px; background: var(--brand-teal);
  }
  .contacts {
    position: absolute; left: 300px; top: 138px; list-style: none;
  }
  .contacts li {
    display: flex; align-items: center; gap: 8px;
    font-size: 13.5px; color: var(--ink); line-height: 21px;
  }
  .contacts svg { width: 11px; height: 11px; flex: none; }
  .address {
    position: absolute; left: 150px; bottom: 34px;
    font-size: 14.5px; color: var(--ink);
  }
</style>
</head>
<body>
<main class="stage">
  <section class="card card--front">
    <div class="brand-name">Quell</div>
    <div class="holder">
      <div class="holder__name">Dara Whitlow</div>
      <div class="holder__title">Managing Director</div>
    </div>
    <div class="divider"></div>
    <ul class="contacts">
      <li>
        <svg viewBox="0 0 12 12"><circle cx="6" cy="6" r="6" fill="var(--name-blue)"/><path d="M4 3.2 L5.2 4.6 L4.6 5.3 Q5.4 6.7 6.7 7.4 L7.4 6.8 L8.8 8 L8 8.9 Q5 8.4 3.2 4 Z" fill="#fff"/></svg>
        +014 226 5180
      </li>
      <li>
        <svg viewBox="0 0 12 12"><circle cx="6" cy="6" r="6" fill="var(--name-blue)"/><rect x="3" y="4" width="6" height="4.2" fill="#fff"/><path d="M3 4 L6 6.4 L9 4" stroke="var(--name-blue)" stroke-width="0.8" fill="none"/></svg>
        info@quellhq.com
      </li>
      <li>
        <svg viewBox="0 0 12 12"><circle cx="6" cy="6" r="6" fill="var(--name-blue)"/><circle cx="6" cy="6" r="3.2" fill="none" stroke="#fff" stroke-width="0.9"/><path d="M2.8 6 H9.2 M6 2.8 V9.2" stroke="#fff" stroke-width="0.8"/></svg>
        www.quellhq.com
      </li>
    </ul>
    <p class="address">18 Harbor Lane, Meridian City, Country - 40217</p>
  </section>

  <section class="card card--back">
    <div class="brand-name">Quell</div>
  </section>
</main>
</body>
</html>
```